Business card design needed

A laid back coffee shop that has a great feel, that becomes a bar and grill at night. We are also wanting to cater for functions etc.
The business itself is painted dark blue/charcoal and has red doors.
Would like a logo that will be recognised when seen.

Industry/Entity Type

Coffee Shop

Contact Information for Business Card

The Lantern Coffee Bar & Grill
14b Wattle St
Merrindale NSW 2291
Ph. 02 4817 6230

Logo Text

Logo styles of interest
Emblem Logo
Abstract Logo
Wordmark Logo
Requirements
Must have
• A loyalty card on the back with 2 rows of 7 stamp spaces and a place to write a name and phone number (for a draw)

```html
<!DOCTYPE html>
<html lang="en">
<head>
<meta charset="utf-8">
<title>The Lantern Coffee Bar &amp; Grill – Loyalty Card</title>
<link rel="stylesheet" href="https://fonts.googleapis.com/css2?family=Delius&display=swap">
<style>
  :root {
    --card-bg: #ffffff;
    --ink: #111111;
    --accent-red: #e0201c;
    --stain-tone: rgba(246, 190, 90, 0.30);
    --stain-fade: rgba(250, 220, 140, 0.12);
  }
  html, body {
    margin: 0;
    padding: 0;
    width: 1200px;
    height: 695px;
    overflow: hidden;
    background: var(--card-bg);
  }
  .loyalty-card {
    position: relative;
    width: 1200px;
    height: 695px;
    background: var(--card-bg);
    font-family: "Delius", cursive;
    color: var(--ink);
    overflow: hidden;
  }
  .stain-area {
    position: absolute;
    left: 560px;
    top: 0;
    width: 520px;
    height: 695px;
    background: radial-gradient(ellipse at 55% 45%,
      var(--stain-tone) 0%,
      var(--stain-fade) 55%,
      transparent 75%);
  }
  .stamp-grid {
    position: absolute;
    left: 0;
    top: 0;
  }
  .stamp-space {
    fill: none;
    stroke: var(--ink);
    stroke-width: 4;
  }
  .entry-field {
    position: absolute;
    left: 90px;
    font-size: 30px;
    display: flex;
    align-items: baseline;
  }
  .entry-field--name { top: 394px; }
  .entry-field--phone { top: 484px; }
  .entry-label { width: 182px; }
  .entry-line {
    width: 673px;
    border-bottom: 2px dashed var(--ink);
    height: 1px;
    transform: translateY(-4px);
  }
  .business-name {
    position: absolute;
    left: 227px;
    top: 586px;
    margin: 0;
    font-size: 40px;
    letter-spacing: 1.5px;
    word-spacing: 10px;
    white-space: nowrap;
  }
  .brand-mark {
    position: absolute;
    left: 985px;
    top: 490px;
    width: 170px;
    text-align: center;
    color: var(--accent-red);
    font-size: 30px;
    line-height: 1.2;
  }
</style>
</head>
<body>
  <main class="loyalty-card">
    <div class="stain-area" role="img" aria-label="Coffee cup ring stain photograph"></div>

    <svg class="stamp-grid" width="1200" height="340" viewBox="0 0 1200 340" aria-label="Stamp spaces, two rows of seven">
      <g class="stamp-row">
        <circle class="stamp-space" cx="148" cy="129" r="59"/>
        <circle class="stamp-space" cx="297" cy="129" r="59"/>
        <circle class="stamp-space" cx="447" cy="129" r="59"/>
        <circle class="stamp-space" cx="597" cy="129" r="59"/>
        <circle class="stamp-space" cx="747" cy="129" r="59"/>
        <circle class="stamp-space" cx="897" cy="129" r="59"/>
        <circle class="stamp-space" cx="1051" cy="129" r="59"/>
      </g>
      <g class="stamp-row">
        <circle class="stamp-space" cx="148" cy="271" r="59"/>
        <circle class="stamp-space" cx="297" cy="271" r="59"/>
        <circle class="stamp-space" cx="447" cy="271" r="59"/>
        <circle class="stamp-space" cx="597" cy="271" r="59"/>
        <circle class="stamp-space" cx="747" cy="271" r="59"/>
        <circle class="stamp-space" cx="897" cy="271" r="59"/>
        <circle class="stamp-space" cx="1051" cy="271" r="59"/>
      </g>
    </svg>

    <div class="entry-field entry-field--name">
      <span class="entry-label">Name</span>
      <span class="entry-line"></span>
    </div>
    <div class="entry-field entry-field--phone">
      <span class="entry-label">Phone</span>
      <span class="entry-line"></span>
    </div>

    <p class="business-name">THE LANTERN Coffee Bar &amp; Grill</p>

    <div class="brand-mark">THE<br>LANTERN</div>
  </main>
</body>
</html>
```